Business card design for holistic health care clinic

We need a double-sided business card design for our holistic health care clinic that integrates our logo design and also its color scheme. My business is called Valmira. It is an integrative medicine clinic. You have already done the logo for me. Please ensure an elegant and upscale design that is not cluttered, but still has all the necessary information (please see below for details).

Target Market(s)

Wellness, fitness, rehabilitation for educated, well-traveled open-minded clients who are focused on natural, organic, balanced and preventive healthcare and lifestyle.

Industry/Entity Type

Medical

Contact Information for Business Card

Modern, clean.

Number of Pages Required

1 page

Font styles to use
Serif
Sans Serif

Colors

Designer to choose colors to be used in the design.

Requirements
Must have
• Logo on one side, all other information on the other side.
• Other information should include:
• Tobias Wrenfeld - DOE, CPT, LMT
• 4100 East Marrow Drive
• Austin, TX 78119
• 512 555 0148
• 818 555 0192
• info@ValmiraHealth.example
• t.wrenfeld@ValmiraHealth.example
Nice to have
• Darker background on front - but not totally black - shaded/dark gray.

```html
<!DOCTYPE html>
<html lang="en">
<head>
<meta charset="utf-8">
<title>Valmira Business Cards</title>
<link href="https://fonts.googleapis.com/css2?family=Nunito+Sans:wght@400;700;800&display=swap" rel="stylesheet">
<style>
  :root {
    --backdrop: #262626;
    --card-gray: #a4a4a4;
    --card-white: #f1f1f1;
    --brand-blue: #0a8fcc;
    --text-light: #ffffff;
    --rule: #7d7d7d;
  }
  * { margin: 0; padding: 0; box-sizing: border-box; }
  html, body {
    width: 1200px; height: 961px; overflow: hidden;
    background: var(--backdrop);
    font-family: "Nunito Sans", sans-serif;
  }
  .sheet { position: relative; width: 1200px; height: 961px; }
  .card {
    position: absolute; top: 220px;
    width: 297px; height: 520px;
    background: var(--card-gray);
  }
  .card--white { background: var(--card-white); }
  .card--front { left: 150px; }
  .card--back-gray { left: 465px; }
  .card--back-white { left: 782px; }
  .brand-name {
    position: absolute; left: 0; right: 0;
    text-align: center;
    color: var(--brand-blue);
    font-weight: 800;
    font-size: 46px;
    letter-spacing: 1px;
    line-height: 1;
    text-transform: uppercase;
  }
  .card--front .brand-name { top: 74px; }
  .card--back-gray .brand-name,
  .card--back-white .brand-name { top: 225px; }
  .contact-block {
    position: absolute; left: 0; right: 0; top: 274px;
    text-align: center;
  }
  .person-name {
    color: var(--brand-blue);
    font-weight: 700; font-size: 27px;
    letter-spacing: -0.5px; line-height: 1;
    text-transform: uppercase;
  }
  .credentials {
    color: var(--brand-blue);
    font-weight: 700; font-size: 14px;
    margin-top: 6px;
  }
  .divider {
    width: 20px; height: 1px;
    background: var(--rule);
    margin: 15px auto;
  }
  .address, .lines {
    color: var(--text-light);
    font-size: 12.5px; line-height: 16px;
  }
  .lines .label { color: var(--brand-blue); font-weight: 700; }
  .card-band {
    position: absolute; left: 0; right: 0; bottom: 0;
    height: 39px;
    background: var(--brand-blue);
    color: var(--text-light);
    font-weight: 700; font-size: 12.5px;
    display: flex; align-items: center; justify-content: center;
  }
</style>
</head>
<body>
<main class="sheet">
  <section class="card card--front">
    <div class="brand-name">Valmira</div>
    <div class="contact-block">
      <div class="person-name">Tobias Wrenfeld</div>
      <div class="credentials">DOE, CPT, LMT</div>
      <div class="divider"></div>
      <div class="address">4100 East Marrow Drive<br>Austin, TX 78119</div>
      <div class="divider"></div>
      <div class="lines">
        <div><span class="label">P.</span> 512 555 0148</div>
        <div><span class="label">M.</span> 818 555 0192</div>
        <div><span class="label">E.</span> t.wrenfeld@ValmiraHealth.example</div>
      </div>
    </div>
    <div class="card-band">www.ValmiraHealth.example</div>
  </section>

  <section class="card card--back-gray">
    <div class="brand-name">Valmira</div>
    <div class="card-band">Helping the body help itself</div>
  </section>

  <section class="card card--white card--back-white">
    <div class="brand-name">Valmira</div>
    <div class="card-band">Helping the body help itself</div>
  </section>
</main>
</body>
</html>
```